Brambleton Pizza Website

We are working with Brambleton Pizza and designing them a website.

Some sites to use for content/competitors and inspiration:

https://fennimores.com
https://www.bhq-eats.com
https://brightorchard.com/en-us/

Thank you for taking the time to consider designing a website for us. We are web developers based in Stockton, CA, USA. Most of our projects go through the same process. Understanding this process may help you win a project with us. We custom-code all of our websites in-house. We don’t have any requirements as to what tools you use for your design, but we prefer Figma files. For any design that we label as four-stars, we send it to the client for review. The client picks the final design they want us to use. Once we complete this process, we will continue to show additional clients all the four-star sites and purchase them later. Your designs will have multiple chances to sell. For better chances of success, we ask that you follow these guidelines.

IMAGES:
If you use any images or icons in the design, we ask that you have a link to the asset so we can purchase the image/icon. Most of the designs we submit do not have the customer’s images on them unless they have some great images. Be creative; show us the feeling you are trying to portray with your image choices. Use any royalty-free site you choose. We subscribe to Quillstone and mainly use their images, but we can purchase images outside of Quillstone.

PLEASE NOTE: we will not submit designs to clients with watermarks on the images.

FONTS:
We ask that you identify the fonts used in the design. This can be done in a message if you want. We typically use Google Fonts and Quillstone Fonts.

CONTENT:
We're always open to different content and ideas. We often submit designs with stock images so the client can see our vision. We typically take pictures after the website launch to use their images with our vision. Lorem Ipsum is fine for paragraphs, but we ask that you write the headers in correct English. We want to be able to show the vision and identify the sections of the website.

INSPIRATION:
We typically add a couple of links in the brief of websites we like to help you get started in your design.

REVISIONS:
We do not often ask for revisions of the designs unless we see something in the design that may not appeal to the client. If there are slight changes that we want to make, we do that in the development process.

FEEDBACK:
We rarely give feedback on designs during the design process. We are working on many website projects and do not have the time to provide feedback. We usually respond if your request is well thought out and asks specific questions, but a note asking “feedback, please” usually goes unanswered.

```html
<!DOCTYPE html>
<html lang="en">
<head>
<meta charset="utf-8">
<title>Brambleton Pizza</title>
<link href="https://fonts.googleapis.com/css2?family=Poppins:wght@300;400;500;600&family=Montserrat:wght@700;800&display=swap" rel="stylesheet">
<style>
:root{
  --red:#e31d1a;
  --green:#3ea836;
  --ink:#1e1e1e;
  --muted:#444;
  --light:#efedee;
  --about:#ebe7e8;
  --dark:#141212;
  --white:#fff;
}
*{margin:0;padding:0;box-sizing:border-box}
html,body{width:1200px;height:5277px;overflow:hidden;background:var(--white)}
body{font-family:'Poppins',sans-serif;color:var(--ink);position:relative}
.abs{position:absolute}
.center{left:0;width:100%;text-align:center}
.btn{position:absolute;display:flex;align-items:center;justify-content:center;border-radius:30px;background:var(--red);color:var(--white);font-size:14px;font-family:'Poppins',sans-serif}
.eyebrow{font-size:15px;color:var(--green);text-transform:uppercase;display:flex;align-items:center;gap:6px;justify-content:center}
.eyebrow::before,.eyebrow::after{content:"";width:30px;height:1px;background:var(--green)}
.section-title{font-size:48px;font-weight:400}

/* hero */
.hero{position:absolute;left:0;top:0;width:1200px;height:713px;background:radial-gradient(ellipse at 75% 55%,#b8512c 0%,#7a2f18 35%,#3a1f14 70%,#1d1410 100%)}
.hero-photo{position:absolute;inset:0;background:radial-gradient(circle at 18% 75%,#c98a4a 0%,rgba(150,70,30,.6) 22%,transparent 40%),radial-gradient(circle at 88% 45%,#d0602e 0%,rgba(160,60,25,.5) 25%,transparent 45%)}
.topbar{position:absolute;left:0;top:0;width:1200px;height:154px;background:rgba(20,16,14,.55)}
.brand{position:absolute;left:80px;top:56px;display:flex;align-items:center;gap:10px;color:var(--white);font-size:22px;font-weight:500}
.brand-dot{width:28px;height:28px;border-radius:50%;background:var(--white)}
.nav{position:absolute;top:102px;display:flex;left:0;width:1200px}
.nav a{position:absolute;transform:translateX(-50%);color:var(--white);text-decoration:none;font-size:13px;white-space:nowrap}
.nav a.active{color:var(--red)}
.nav a.active::after{content:"";position:absolute;left:0;right:0;bottom:-9px;height:2px;background:var(--red)}
.search{position:absolute;left:843px;top:39px;width:175px;height:33px;border:1.5px solid var(--white);border-radius:20px;color:var(--red);font-size:11px;padding:8px 16px}
.hero-card{position:absolute;left:246px;top:197px;width:709px;height:434px;border-radius:60px;background:rgba(240,236,236,.72);text-align:center}
.hero-card h1{font-size:66px;font-weight:400;line-height:88px;margin-top:60px;color:#111}
.hero-card p{font-size:13px;line-height:18px;width:590px;margin:26px auto 0;color:#222}
.hero-card .btn{top:317px;height:46px;font-size:17px}
.btn-ghost{background:transparent;border:2px solid var(--red);color:#222}

/* stats */
.stats{position:absolute;top:713px;left:0;width:1200px;height:352px;background:var(--light)}
.stat{position:absolute;top:90px;width:240px;transform:translateX(-50%);text-align:center}
.stat-icon{width:133px;height:131px;margin:0 auto;background:var(--green);border-radius:6px;display:flex;align-items:center;justify-content:center}
.stat-num{color:var(--red);font-size:38px;font-weight:600;margin-top:12px;line-height:48px}
.stat-label{font-size:20px;line-height:26px}

/* menus */
.menus{position:absolute;top:1065px;left:0;width:1200px;height:1208px}
.card{position:absolute;width:320px;height:317px;border-radius:40px;background:#ececec;box-shadow:0 6px 8px rgba(0,0,0,.18);text-align:center}
.card-photo{position:absolute;left:72px;top:-88px;width:176px;height:176px;border-radius:50%;background:radial-gradient(circle,#d8743a 0%,#c85a28 45%,#a8782f 75%,#f2ddc0 78%,#f2ddc0 88%,#5c5a56 90%);box-shadow:0 4px 6px rgba(0,0,0,.25)}
.card h3{font-size:20px;font-weight:400;margin-top:113px}
.card p{font-size:13px;line-height:17px;width:250px;margin:9px auto 0;color:#333}
.card .btn{left:96px;top:241px;width:127px;height:35px;font-size:13px}

/* about */
.about{position:absolute;top:2273px;left:0;width:1200px;height:543px;background:var(--about)}
.eyebrow-left{font-size:15px;color:var(--green);display:flex;align-items:center;gap:6px}
.eyebrow-left::after{content:"";width:30px;height:1px;background:var(--green)}
.about-photo{position:absolute;left:666px;top:56px;width:430px;height:430px;border-radius:50%;background:radial-gradient(circle,#c7432a 0%,#b8502a 50%,#c27b34 80%,#8a4f22 100%);box-shadow:0 6px 14px rgba(0,0,0,.3)}

/* offers */
.offers{position:absolute;top:2816px;left:0;width:1200px;height:461px;overflow:hidden;background:radial-gradient(ellipse at 70% 50%,#2a2220 0%,#151111 60%,#0d0b0b 100%);color:var(--white)}
.offer-pizza{position:absolute;z-index:1;border-radius:50%;background:radial-gradient(circle,#d4552c 0%,#c66730 55%,#d29444 80%,#7a4920 100%)}
.offer-text{position:absolute;z-index:2}
.offer-headline{left:66px;top:100px;font-family:'Montserrat',sans-serif;font-weight:800;font-size:74px;line-height:95px;letter-spacing:-0.5px;white-space:nowrap}

/* testimonials */
.testimonials{position:absolute;top:3277px;left:0;width:1200px;height:538px;background:radial-gradient(ellipse at 50% 50%,#f4f2f2 0%,#ebe6e5 70%,#e0d6d3 100%)}
.arrow{position:absolute;top:3610px}

/* newsletter */
.newsletter{position:absolute;top:3815px;left:0;width:1200px;height:342px;background:radial-gradient(ellipse at 30% 50%,#2b1f1a 0%,#120e0c 70%);color:var(--white);text-align:center}
.email-field{position:absolute;left:150px;top:213px;width:706px;height:52px;background:var(--white);color:#777;font-size:16px;text-align:left;padding:14px 22px}
.email-submit{position:absolute;left:856px;top:213px;width:172px;height:52px;background:var(--red);color:var(--white);font-size:16px;display:flex;align-items:center;justify-content:center}

/* contact */
.contact{position:absolute;top:4157px;left:0;width:1200px;height:625px}
.contact-photo{position:absolute;left:135px;top:260px;width:418px;height:306px;background:radial-gradient(circle at 45% 45%,#d9a04a 0%,#b9722e 40%,#4b3020 75%,#1a1412 100%)}
.field{position:absolute;border:1px solid #ddd;color:#aaa;font-size:13px;padding:14px 12px;box-shadow:0 1px 3px rgba(0,0,0,.08)}

/* footer */
.footer{position:absolute;top:4782px;left:0;width:1200px;height:495px;background:#121010;color:var(--white)}
.footer h4{position:absolute;font-size:19px;font-weight:500}
.footer h4::after{content:"";position:absolute;left:0;bottom:-6px;width:38px;height:2px;background:var(--red)}
.flink{position:absolute;left:530px;font-size:15px}
.flink::before{content:"";position:absolute;left:-20px;top:8px;width:6px;height:6px;border-radius:50%;background:var(--red)}
.ficon{position:absolute;left:814px;width:36px;height:36px;border-radius:50%;background:var(--white);display:flex;align-items:center;justify-content:center}
.ftext{position:absolute;left:862px;font-size:15px;line-height:26px}
.social{position:absolute;top:269px;width:36px;height:36px;border-radius:50%;background:var(--white)}
</style>
</head>
<body>

<header class="hero">
  <div class="hero-photo" role="img" aria-label="Close-up of pepperoni and basil pizzas on a wooden table"></div>
  <div class="topbar"></div>
  <div class="brand"><span class="brand-dot"></span>Brambleton Pizza</div>
  <nav class="nav">
    <a class="active" style="left:461px">Home</a>
    <a style="left:551px">Our Menus</a>
    <a style="left:663px">About Us</a>
    <a style="left:772px">Order Online</a>
    <a style="left:872px">Gallery</a>
    <a style="left:973px">Reviews</a>
    <a style="left:1079px">Contact Us</a>
  </nav>
  <div class="search">Search
    <svg class="abs" style="right:14px;top:7px" width="18" height="18" viewBox="0 0 18 18" fill="none" stroke="#fff" stroke-width="2"><circle cx="7.5" cy="7.5" r="5.5"/><path d="M12 12l4.5 4.5"/></svg>
  </div>
  <svg class="abs" style="left:1037px;top:38px" width="28" height="28" viewBox="0 0 28 28" fill="none" stroke="#fff" stroke-width="2"><path d="M2 4h4l3 14h14l3-10H8"/><circle cx="11" cy="23" r="2"/><circle cx="21" cy="23" r="2"/></svg>
  <span class="abs" style="left:1058px;top:36px;width:10px;height:10px;border-radius:50%;background:var(--red)"></span>
  <svg class="abs" style="left:1088px;top:38px" width="28" height="30" viewBox="0 0 28 30" fill="none" stroke="#fff" stroke-width="2"><circle cx="14" cy="9" r="7"/><path d="M2 29c0-7 5-11 12-11s12 4 12 11"/></svg>

  <div class="hero-card">
    <h1>A Slice Of Heaven<br>In Every Bite pizza</h1>
    <p>Lorem ipsum dolor sit amet, consectetur adipiscing elit, sed do eiusmod tempor incididunt ut labore et dolore magna aliqua.</p>
    <span class="btn" style="left:123px;width:223px">Book A Table</span>
    <span class="btn btn-ghost" style="left:364px;width:222px">View Menu</span>
  </div>
</header>

<section class="stats">
  <div class="stat" style="left:233px">
    <div class="stat-icon"><svg width="70" height="70" viewBox="0 0 70 70" fill="none" stroke="#fff" stroke-width="3"><path d="M24 60s-14-16-14-27a14 14 0 0 1 28 0c0 11-14 27-14 27z"/><circle cx="24" cy="33" r="5"/><path d="M52 28s-8-9-8-15a8 8 0 0 1 16 0c0 6-8 15-8 15z"/><path d="M32 58c8 0 18-6 20-22" stroke-dasharray="3 4"/></svg></div>
    <div class="stat-num">50</div><div class="stat-label">Pizza Branches</div>
  </div>
  <div class="stat" style="left:481px">
    <div class="stat-icon"><svg width="80" height="80" viewBox="0 0 80 80" fill="none" stroke="#fff" stroke-width="3"><circle cx="40" cy="38" r="20"/><path d="M40 26l4 8 9 1-7 6 2 9-8-5-8 5 2-9-7-6 9-1z" fill="#fff"/><path d="M14 30c-3 14 4 26 16 32M66 30c3 14-4 26-16 32"/></svg></div>
    <div class="stat-num">30</div><div class="stat-label">Number of Awards</div>
  </div>
  <div class="stat" style="left:729px">
    <div class="stat-icon"><svg width="80" height="80" viewBox="0 0 80 80" fill="#fff"><circle cx="40" cy="38" r="10"/><path d="M20 70c0-12 9-20 20-20s20 8 20 20z"/><circle cx="56" cy="62" r="9" stroke="var(--green)" stroke-width="2"/><path d="M52 62l3 3 6-6" stroke="var(--green)" stroke-width="2.5" fill="none"/><path d="M40 8l2 5 5 .5-4 3 1 5-4-3-4 3 1-5-4-3 5-.5zM22 16l1.5 4 4 .3-3 2.5 1 4-3.5-2-3.5 2 1-4-3-2.5 4-.3zM58 16l1.5 4 4 .3-3 2.5 1 4-3.5-2-3.5 2 1-4-3-2.5 4-.3z"/></svg></div>
    <div class="stat-num">100</div><div class="stat-label">Happy Customer</div>
  </div>
  <div class="stat" style="left:977px">
    <div class="stat-icon"><svg width="80" height="80" viewBox="0 0 80 80" fill="#fff"><circle cx="40" cy="28" r="8"/><circle cx="24" cy="34" r="7"/><circle cx="56" cy="34" r="7"/><circle cx="32" cy="46" r="7"/><circle cx="48" cy="46" r="7"/><path d="M14 58c0-8 6-13 12-13s10 4 10 10zM44 55c0-6 4-10 10-10s12 5 12 13zM22 66c0-8 5-12 10-12s10 4 10 12zM38 66c0-8 5-12 10-12s10 4 10 12z"/></svg></div>
    <div class="stat-num">30</div><div class="stat-label">Staff</div>
  </div>
</section>

<section class="menus">
  <div class="abs center" style="top:74px"><div class="eyebrow">Order Online Now</div></div>
  <h2 class="abs center section-title" style="top:88px">Our Menus</h2>

  <article class="card" style="left:88px;top:287px"><div class="card-photo" role="img" aria-label="Italian pizza viewed from above"></div><h3>Italian Pizza</h3><p>Lorem ipsum dolor sit amet, consectetur adipiscing elit, sed do eiusmod tempor incididunt .</p><span class="btn">Read More</span></article>
  <article class="card" style="left:440px;top:287px"><div class="card-photo" role="img" aria-label="Roman pizza viewed from above"></div><h3>Roman Pizza</h3><p>Lorem ipsum dolor sit amet, consectetur adipiscing elit, sed do eiusmod tempor incididunt .</p><span class="btn">Read More</span></article>
  <article class="card" style="left:793px;top:287px"><div class="card-photo" role="img" aria-label="Vegetable pizza viewed from above"></div><h3>veg Pizza</h3><p>Lorem ipsum dolor sit amet, consectetur adipiscing elit, sed do eiusmod tempor incididunt .</p><span class="btn">Read More</span></article>

  <article class="card" style="left:88px;top:762px"><div class="card-photo" role="img" aria-label="Cheese pizza viewed from above"></div><h3>Cheese Pizza</h3><p>Lorem ipsum dolor sit amet, consectetur adipiscing elit, sed do eiusmod tempor incididunt .</p><span class="btn">Read More</span></article>
  <article class="card" style="left:440px;top:762px"><div class="card-photo" role="img" aria-label="BBQ chicken pizza viewed from above"></div><h3>BBQ Chicken Pizza</h3><p>Lorem ipsum dolor sit amet, consectetur adipiscing elit, sed do eiusmod tempor incididunt .</p><span class="btn">Read More</span></article>
  <article class="card" style="left:793px;top:762px"><div class="card-photo" role="img" aria-label="Stuffed crust pizza viewed from above"></div><h3>Stuffed crust</h3><p>Lorem ipsum dolor sit amet, consectetur adipiscing elit, sed do eiusmod tempor incididunt .</p><span class="btn">Read More</span></article>

  <span class="btn" style="left:516px;top:1132px;width:160px;height:41px;font-size:16px">View More</span>
</section>

<section class="about">
  <div class="abs eyebrow-left" style="left:145px;top:122px">WHO WE ARE</div>
  <h2 class="abs section-title" style="left:145px;top:136px">About Us</h2>
  <p class="abs" style="left:145px;top:222px;width:430px;font-size:13.5px;line-height:22.5px;color:#333">Sed ut perspiciatis unde omnis iste natus error sit voluptatem accusantium doloremque laudantium, totam rem aperiam, eaque ipsa quae ab illo inventore veritatis et quasi architecto beatae vitae dicta sunt explicabo. Nemo enim ipsam voluptatem quia voluptas sit aspernatur aut odit aut fugit, sed quia consequuntur magni dolores eos qui ratione voluptatem sequi nesciunt.</p>
  <span class="btn" style="left:147px;top:399px;width:123px;height:34px;font-size:13px">Read More</span>
  <div class="about-photo" role="img" aria-label="Whole pepperoni pizza with tomato and basil"></div>
</section>

<section class="offers">
  <div class="offer-pizza" role="img" aria-label="Large loaded pizza" style="left:800px;top:24px;width:380px;height:380px"></div>
  <div class="offer-pizza" role="img" aria-label="Smaller pizza beside it" style="left:728px;top:224px;width:210px;height:210px;box-shadow:0 0 18px rgba(0,0,0,.6)"></div>
  <div class="offer-text" style="left:68px;top:36px;font-size:56px;font-weight:300;white-space:nowrap">Amazing Offers Online</div>
  <div class="offer-text offer-headline">50% OFF PIZZAS<br>ONLINE</div>
  <p class="offer-text" style="left:68px;top:312px;width:560px;font-size:13px;line-height:17px">Lorem ipsum dolor sit amet, consectetur adipiscing elit, sed do eiusmod tempor incididunt ut labore et dolore magna aliqua.</p>
  <span class="btn" style="left:68px;top:364px;width:141px;height:43px;font-size:16px;z-index:2">Order Now</span>
</section>

<section class="testimonials">
  <div class="abs center" style="top:106px"><div class="eyebrow">Our Reviews</div></div>
  <h2 class="abs center section-title" style="top:122px">Testimonials</h2>
  <svg class="abs" style="left:558px;top:220px" width="80" height="62" viewBox="0 0 80 62" fill="var(--red)"><path d="M0 62V34C0 14 10 3 30 0l3 8C22 12 17 20 17 30h15v32zM46 62V34C46 14 56 3 76 0l3 8C68 12 63 20 63 30h15v32z"/></svg>
  <p class="abs" style="left:300px;top:308px;width:600px;text-align:center;font-size:13.5px;line-height:22px;color:#222">Lorem ipsum dolor sit amet, consectetur adipiscing elit, sed do eiusmod tempor incididunt ut labore et dolore magna aliqua. Quis ipsum suspendisse ultrices gravida. Risus commodo viverra maecenas accumsan lacus vel facilisis.</p>
  <div class="abs center" style="top:395px;font-size:14px;font-weight:500">MARLOW HENDRY</div>
  <div class="abs center" style="top:418px;font-size:22px;color:#e9b42a;letter-spacing:1px">★★★★★</div>
</section>
<svg class="arrow" style="left:228px" width="20" height="30" viewBox="0 0 20 30" fill="none" stroke="var(--red)" stroke-width="4"><path d="M16 2L4 15l12 13"/></svg>
<svg class="arrow" style="left:952px" width="20" height="30" viewBox="0 0 20 30" fill="none" stroke="var(--red)" stroke-width="4"><path d="M4 2l12 13L4 28"/></svg>

<section class="newsletter">
  <h2 class="abs center" style="top:58px;font-size:44px;font-weight:500">SUBSCRIBE TO OUR NEWSLETTER</h2>
  <p class="abs center" style="top:140px;font-size:19px">Be the first to know about new products and exclusive offers.</p>
  <div class="email-field">Enter a valid email address</div>
  <div class="email-submit">SUBMIT</div>
</section>

<section class="contact">
  <div class="abs center" style="top:90px"><div class="eyebrow">Get In Touch With</div></div>
  <h2 class="abs center section-title" style="top:106px">Contact Us</h2>
  <p class="abs center" style="top:187px;font-size:15.5px;color:#222">For more information,Please fill out the following and we will be in touch shortly</p>
  <div class="contact-photo" role="img" aria-label="Vegetable pizza with olives and peppers on a dark table"></div>
  <div class="field" style="left:614px;top:260px;width:215px;height:50px">First Name</div>
  <div class="field" style="left:854px;top:260px;width:215px;height:50px">Second Name</div>
  <div class="field" style="left:614px;top:338px;width:215px;height:51px">Phone</div>
  <div class="field" style="left:854px;top:338px;width:215px;height:51px">Subject</div>
  <div class="field" style="left:614px;top:412px;width:459px;height:100px;padding-top:38px">Message</div>
  <span class="btn" style="left:614px;top:533px;width:91px;height:31px;font-size:13px">Submit</span>
</section>

<footer class="footer">
  <div class="abs" style="left:150px;top:160px;width:200px;display:flex;align-items:center;justify-content:center;gap:10px;font-size:22px;font-weight:500"><span class="brand-dot"></span>Brambleton</div>
  <div class="abs" style="left:150px;top:196px;width:200px;text-align:center;font-size:16px;font-weight:500">Pizza</div>
  <span class="social" style="left:181px"></span>
  <span class="social" style="left:230px"></span>
  <span class="social" style="left:279px"></span>

  <h4 style="left:508px;top:100px">LINKS</h4>
  <span class="flink" style="top:170px">Our Menus</span>
  <span class="flink" style="top:203px">About Us</span>
  <span class="flink" style="top:234px">Order Online</span>
  <span class="flink" style="top:267px">Gallery</span>
  <span class="flink" style="top:299px">Reviews</span>
  <span class="flink" style="top:332px">Contact Us</span>

  <h4 style="left:811px;top:100px">CONTACT US</h4>
  <span class="ficon" style="top:172px"><svg width="16" height="20" viewBox="0 0 16 20" fill="var(--red)"><path d="M8 0a7 7 0 0 0-7 7c0 5 7 13 7 13s7-8 7-13a7 7 0 0 0-7-7zm0 10a3 3 0 1 1 0-6 3 3 0 0 1 0 6z"/></svg></span>
  <span class="ftext" style="top:174px">465, Lorem Ipsum<br>Lorem Ipsum , Lorem Ipsum</span>
  <span class="ficon" style="top:236px"><svg width="18" height="18" viewBox="0 0 18 18" fill="var(--red)"><path d="M4 1l3 4-2 2c1 2 3 4 5 5l2-2 4 3-2 3C8 16 2 10 1 4z"/></svg></span>
  <span class="ftext" style="top:241px">+1 888 888 8888</span>
  <span class="ficon" style="top:287px"><svg width="18" height="14" viewBox="0 0 18 14" fill="var(--red)"><path d="M0 0h18v14H0z"/><path d="M1 1l8 6 8-6" stroke="#fff" stroke-width="1.5" fill="none"/></svg></span>
  <span class="ftext" style="top:292px">help@companyname.com</span>

  <div class="abs" style="left:68px;top:416px;width:1065px;height:1px;background:#555"></div>
  <div class="abs center" style="top:444px;font-size:13px">© 2025 Company Name, Inc. All Rights Reserved.</div>
</footer>

</body>
</html>
```